Business card design needed

OH&S consultancy and training

Industry/Entity Type

Training

Contact Information for Business Card

Coastal Hazard & Learning Collective
Dorian Whitfield
Director

0427 913 058
dorian.whitfield@chlcollect.com.au
chlcollect.com.au

Ph: 03 9172 4039
Fx: 03 9172 4041

```html
<!DOCTYPE html>
<html lang="en">
<head>
<meta charset="utf-8">
<title>Coastal Hazard &amp; Learning Collective – Business Card</title>
<link rel="stylesheet" href="https://fonts.googleapis.com/css2?family=Barlow:wght@400;500;600&display=swap">
<style>
  :root {
    --page-bg: #e6e9ec;
    --card-white: #ffffff;
    --card-navy: #0c2b3c;
    --signal-yellow: #f2e400;
    --ink: #2c2c2c;
    --ink-soft: #4a4a4a;
    --rule: #3a3a3a;
    --brand-grey: #9c9c9c;
    --brand-light: #d8dadc;
  }
  * { box-sizing: border-box; margin: 0; padding: 0; }
  html, body {
    width: 1200px; height: 960px; overflow: hidden;
    background: var(--page-bg);
    font-family: "Barlow", Arial, sans-serif;
  }
  .sheet {
    position: relative; width: 1200px; height: 960px;
    display: flex; flex-direction: column; align-items: center; justify-content: center; gap: 40px;
  }
  .card {
    position: relative; width: 680px; height: 416px;
    box-shadow: 0 6px 18px rgba(0,0,0,0.12);
  }
  .card--front { background: var(--card-white); color: var(--ink); }
  .card--back { background: var(--card-navy); display: flex; align-items: center; justify-content: center; }

  .brand { display: flex; align-items: center; gap: 14px; }
  .brand__mark { width: 26px; height: 26px; background: var(--signal-yellow); flex: none; }
  .brand__name { font-weight: 500; letter-spacing: 0.2px; }
  .card--front .brand { position: absolute; left: 40px; top: 44px; }
  .card--front .brand__name { font-size: 25px; color: var(--brand-grey); }
  .card--back .brand__name { font-size: 30px; color: var(--brand-light); }
  .card--back .brand__mark { width: 32px; height: 32px; }

  .holder { position: absolute; left: 40px; top: 180px; }
  .holder__name { font-size: 36px; font-weight: 400; color: var(--ink); letter-spacing: 0.5px; }
  .holder__role { font-size: 20px; color: var(--ink-soft); margin-top: 8px; letter-spacing: 0.5px; }

  .divider { position: absolute; left: 40px; right: 40px; top: 286px; height: 0; border-top: 1.5px solid var(--rule); }

  .contact-web { position: absolute; left: 40px; top: 318px; font-size: 19px; line-height: 1.5; letter-spacing: 0.4px; }
  .contact-web__site { font-weight: 600; font-size: 20px; }

  .contact-phone { position: absolute; right: 40px; top: 306px; font-size: 17px; line-height: 1.55; letter-spacing: 0.6px; }
  .contact-phone__row { display: flex; gap: 14px; }
  .contact-phone__label { color: var(--signal-yellow); width: 12px; }
</style>
</head>
<body>
  <main class="sheet">
    <section class="card card--front" aria-label="Business card front">
      <div class="brand">
        <span class="brand__mark"></span>
        <span class="brand__name">Coastal Hazard &amp; Learning Collective</span>
      </div>
      <div class="holder">
        <p class="holder__name">Dorian Whitfield</p>
        <p class="holder__role">Director</p>
      </div>
      <div class="divider"></div>
      <div class="contact-web">
        <p class="contact-web__email">dorian.whitfield@chlcollect.com.au</p>
        <p class="contact-web__site">chlcollect.com.au</p>
      </div>
      <div class="contact-phone">
        <p class="contact-phone__row"><span class="contact-phone__label">M</span><span>0427 913 058</span></p>
        <p class="contact-phone__row"><span class="contact-phone__label">T</span><span>03 9172 4039</span></p>
        <p class="contact-phone__row"><span class="contact-phone__label">F</span><span>03 9172 4041</span></p>
      </div>
    </section>

    <section class="card card--back" aria-label="Business card back">
      <div class="brand">
        <span class="brand__mark"></span>
        <span class="brand__name">Coastal Hazard &amp; Learning Collective</span>
      </div>
    </section>
  </main>
</body>
</html>
```